4D Cradle Glimpse Luxury Ultrasound Billboard

Design a HIGH-END, MODERN billboard for my private prenatal ultrasound studio, 4D Cradle Glimpse, located in Brindle Cove, Georgia.
This billboard will be viewed by drivers traveling at highway speeds, so it must be extremely clean, simple, and readable within 6 seconds.
About My Business
4D Cradle Glimpse is a private prenatal ultrasound studio specializing in:
Highest technology 4D/HD Ultrasounds
Early Gender Determination
Pregnancy Confirmation
I have been serving families for nearly 10 years and is known for creating a memorable experience, not just an ultrasound appointment.
Design Style
I DO NOT want:
Flowers
Leaves
Swirls
Glitter
Hearts everywhere
Busy backgrounds
Generic maternity stock graphics
I DO want:
Modern
Luxury
Upscale
Clean
Professional
Eye-catching
Premium medical spa feel
Colors
Use colors from my logo:
LOGO Green ( or a deep green)
Black
White
Soft Gold accents
Images:
Incorporate my professional headshot in a clean, modern way, logo, and the ultrasound images
Text
Keep wording minimal.
Primary Headline ( OPEN TO IDEAS) :
EXAMPLES ( WOULD RATHER SOMETHING MORE CATCHY)
" ADVANCED IMAGING. UNFORGETTABLE MOMENTS"
"MEET YOUR BABY BEFORE BIRTH"
Under headline:
4D Ultrasound • Early Gender • Pregnancy Confirmation
Business Name:
4D Cradle Glimpse
Private Prenatal Ultrasound Studio
Phone Number:
850-471-5923
Important
This billboard must be readable in 5–6 seconds from a moving vehicle.
Less text is better.
The phone number and business name must be visible from a distance.
The design should feel like a premium brand that immediately tells expecting parents:
“This is where I go to see my baby.”
Files Provided
Official logo
Headshot
Ultrasound images
Don’t make this look like a medical office billboard.
Make it look like a luxury baby experience billboard. That’s what separates 4D Cradle Glimpse from hospitals, OB offices, and all the new studios popping up around you. The emotional connection is what gets moms to book. ❤️
Billboard Size - 10.6” x 36”

```html
<!DOCTYPE html>
<html lang="en">
<head>
<meta charset="UTF-8">
<title>4D Cradle Glimpse Billboard</title>
<link rel="stylesheet" href="https://fonts.googleapis.com/css2?family=Poppins:ital,wght@0,400;0,600;0,700;0,800;1,700&display=swap">
<style>
  :root {
    --green: #0a3d2c;
    --green-deep: #062b1f;
    --gold: #e2b84e;
    --gold-soft: #f0cf6e;
    --gold-dark: #b88a2a;
    --white: #ffffff;
    --ink: #1c1c1c;
    --stage: #e8ebe9;
    --photo-light: #eeeeee;
    --photo-mid: #c9cdc9;
    --scan-light: #c98d74;
    --scan-dark: #5a2a1e;
  }
  html, body {
    margin: 0;
    width: 1200px;
    height: 400px;
    overflow: hidden;
    background: var(--stage);
    font-family: "Poppins", sans-serif;
  }
  .billboard {
    position: absolute;
    left: 20px;
    top: 40px;
    width: 1160px;
    height: 321px;
    background: linear-gradient(100deg, var(--green) 0%, var(--green-deep) 100%);
    overflow: hidden;
  }
  .billboard-shapes {
    position: absolute;
    inset: 0;
    width: 1160px;
    height: 321px;
  }
  .headline {
    position: absolute;
    left: 314px;
    top: 6px;
    margin: 0;
    font-weight: 800;
    font-size: 77px;
    line-height: 64px;
    letter-spacing: 1px;
    text-transform: uppercase;
    white-space: nowrap;
  }
  .headline-top { display: block; color: var(--white); }
  .headline-bottom { display: block; color: var(--gold); }
  .headline-rule {
    position: absolute;
    left: 315px;
    top: 150px;
    width: 665px;
    height: 1px;
    background: var(--gold);
    opacity: 0.8;
  }
  .services {
    position: absolute;
    left: 366px;
    top: 154px;
    margin: 0;
    font-style: italic;
    font-weight: 700;
    font-size: 23.5px;
    line-height: 30px;
    color: var(--white);
    white-space: nowrap;
  }
  .services .accent { color: var(--gold); }
  .services .dot {
    display: inline-block;
    width: 10px;
    height: 10px;
    margin: 0 13px 3px;
    border-radius: 50%;
    background: var(--gold);
    vertical-align: middle;
  }
  .brand-card {
    position: absolute;
    left: 404px;
    top: 211px;
    width: 191px;
    height: 95px;
    box-sizing: border-box;
    background: var(--white);
    border: 2px solid #cfcfcf;
    border-radius: 10px;
    display: flex;
    flex-direction: column;
    align-items: center;
    justify-content: center;
    text-align: center;
  }
  .brand-name {
    font-weight: 700;
    font-size: 21px;
    line-height: 24px;
    color: var(--gold-dark);
  }
  .brand-tag {
    margin-top: 8px;
    font-weight: 600;
    font-size: 7.5px;
    letter-spacing: 0.3px;
    color: var(--ink);
  }
  .phone {
    position: absolute;
    left: 614px;
    top: 219px;
    display: flex;
    align-items: center;
    gap: 12px;
  }
  .phone-icon { width: 42px; height: 42px; flex: none; }
  .phone-number {
    font-weight: 700;
    font-size: 48px;
    line-height: 56px;
    color: var(--white);
    letter-spacing: 0.5px;
  }
  .location {
    position: absolute;
    left: 668px;
    top: 279px;
    width: 352px;
    display: flex;
    align-items: center;
    gap: 12px;
    color: var(--white);
    font-weight: 400;
    font-size: 17px;
    line-height: 24px;
    letter-spacing: 1.2px;
    white-space: nowrap;
  }
  .location::before, .location::after {
    content: "";
    flex: 1;
    height: 1px;
    background: var(--gold);
  }
</style>
</head>
<body>
  <section class="billboard">
    <svg class="billboard-shapes" viewBox="0 0 1160 321">
      <defs>
        <linearGradient id="photoTone" x1="0" y1="0" x2="1" y2="1">
          <stop offset="0" stop-color="var(--photo-light)"/>
          <stop offset="0.6" stop-color="var(--photo-mid)"/>
          <stop offset="1" stop-color="#1f4a36"/>
        </linearGradient>
        <radialGradient id="scanTone" cx="0.45" cy="0.45" r="0.6">
          <stop offset="0" stop-color="var(--scan-light)"/>
          <stop offset="1" stop-color="var(--scan-dark)"/>
        </radialGradient>
        <linearGradient id="goldSweep" x1="0" y1="0" x2="1" y2="1">
          <stop offset="0" stop-color="var(--gold-soft)"/>
          <stop offset="0.5" stop-color="var(--gold)"/>
          <stop offset="1" stop-color="var(--gold-dark)"/>
        </linearGradient>
      </defs>
      <path class="headshot-area" role="img" aria-label="Professional headshot of the studio owner in green scrubs holding an ultrasound probe beside an ultrasound machine"
            d="M0 0 H218 C256 40 252 140 214 205 C192 245 176 285 165 321 H0 Z" fill="url(#photoTone)"/>
      <path d="M218 0 C256 40 252 140 214 205 C192 245 176 285 165 321" fill="none" stroke="var(--gold)" stroke-width="2"/>
      <circle class="scan-area" role="img" aria-label="Close-up 4D ultrasound image of a baby" cx="268" cy="223" r="91" fill="url(#scanTone)" stroke="var(--gold)" stroke-width="3"/>
      <path class="gold-sweep" d="M1160 96 C1115 150 1090 240 1089 321 H1160 Z" fill="url(#goldSweep)"/>
    </svg>

    <h1 class="headline">
      <span class="headline-top">Meet Your</span>
      <span class="headline-bottom">Baby Before Birth</span>
    </h1>
    <div class="headline-rule"></div>

    <p class="services"><span class="accent">4D</span> Ultrasound<span class="dot"></span>Early Gender<span class="dot"></span>Pregnancy Confirmation</p>

    <div class="brand-card">
      <span class="brand-name">4D Cradle Glimpse</span>
      <span class="brand-tag">PRENATAL ULTRASOUND STUDIO</span>
    </div>

    <div class="phone">
      <svg class="phone-icon" viewBox="0 0 42 42" aria-hidden="true">
        <circle cx="21" cy="21" r="20" fill="var(--gold)"/>
        <path d="M14 11 l4 -1 l3 6 l-3 2 c1 3 3 5 6 6 l2 -3 l6 3 l-1 4 c-1 2 -3 2 -5 2 c-8 -2 -13 -7 -14 -14 c0 -2 0 -4 2 -5 z" fill="var(--green)"/>
        <path d="M24 11 a7 7 0 0 1 7 7 M24 15 a3 3 0 0 1 3 3" fill="none" stroke="var(--green)" stroke-width="2" stroke-linecap="round"/>
      </svg>
      <span class="phone-number">850-471-5923</span>
    </div>
    <div class="location">Brindle Cove, Georgia</div>
  </section>
</body>
</html>
```